Tralha Cesto Website

Tralha Cesto is a brazilian Self Storage in a Box where customers can store all the clutter that they have out of their houses. We deliver one or more boxes at their homes, they fill the boxes with their stuff and we store it for them.

"Tralha" means something like "mess" in portuguese. So the name would means something like "Mess Box" or "Clutter Box".

How it works:
1) The customer asks for 1 or more boxes.
2) Tralha Cesto leaves the boxes at their houses
3) The clients fill the boxes with their stuff
4) Customers call Tralha Cesto for the pick up
5) We get the boxes and store them
6) When the customer wants the box back they can order it online or by phone and wait for the box delivery.
-

We have already produced a flyer to launch the service. You can see this flyer at "Project Files".

We want the website to have a startup "look and fell". Here are some websites of similar services that we like very much.
- www.crateowl.example
- www.stowpod.example

We are planning this launching website to have only 2 pages. The Landing Page and a FAQ page. We are producing an explainer video. The proposed designs must think about a special place to place the video.

We are still writing it´s content but you can use the flyer as a reference.

Thanks.
Updates

Project Deadline Extended
Reason: The project was refundable but as we have already received good design options, now we are turning it to Non Refundable and giving more time for new designers to send their proposals. Thanks.

Project Deadline Extended

Target Market(s)

Young couples having kids
Students
Families in need of more space at home

Industry/Entity Type

Store

Requirements
Must have
• Special place to place the explainer video (still being produced).

How it works drawing. You can use the one on the flyer or draw a new one (recomended).

Transparent box drawings (showing it´s content). I will serve to show the clients what they can store with the service.

Clutter Room Before/After Pic/drawings (showing how the service can benefit the client).

```html
<!DOCTYPE html>
<html lang="pt-BR">
<head>
<meta charset="utf-8">
<title>Tralha Cesto — Storage made simple</title>
<link href="https://fonts.googleapis.com/css2?family=Open+Sans:wght@400;600;700;800&display=swap" rel="stylesheet">
<style>
:root{
  --blue:#1f6fc0;
  --blue-dark:#175a9e;
  --ink:#2b2b2b;
  --muted:#6d6d6d;
  --hero-dark:#33373c;
  --orange:#f5a31a;
  --orange-deep:#e8890c;
  --panel-grey:#555a60;
  --light:#f2f2f2;
  --line:#d9d9d9;
  --footer:#2e3236;
  --footer-bottom:#25282b;
  --white:#ffffff;
}
*{box-sizing:border-box;margin:0;padding:0}
html,body{width:1200px;height:2568px;overflow:hidden}
body{font-family:"Open Sans",Arial,sans-serif;color:var(--ink);background:var(--white);position:relative}
.wrap{width:1000px;margin:0 auto;position:relative}

/* header */
.site-header{height:70px;background:var(--white);border-bottom:1px solid var(--line)}
.site-header .wrap{display:flex;align-items:center;justify-content:space-between;height:70px}
.brand{display:flex;align-items:center;gap:10px;font-weight:700;font-size:20px;color:var(--blue)}
.brand-mark{width:26px;height:26px;background:var(--blue);border-radius:50%}
.main-nav{display:flex;align-items:center;height:70px}
.main-nav a{font-size:12px;font-weight:700;color:#555;text-decoration:none;padding:0 13px;height:70px;display:flex;align-items:center}
.main-nav a.active{color:var(--blue);border-bottom:3px solid var(--blue)}
.main-nav .search{margin-left:12px;padding-left:16px;border-left:1px solid var(--line)}

/* hero */
.hero{height:350px;display:flex;position:relative}
.hero-left{width:50%;background:linear-gradient(160deg,#3b4046,#2a2d31);display:flex;flex-direction:column;justify-content:center;padding-left:120px;color:var(--white)}
.hero-left h1{font-size:30px;font-weight:700;letter-spacing:1px}
.hero-left .rule{width:330px;height:2px;background:rgba(255,255,255,.6);margin:18px 0}
.hero-left p{font-size:24px;font-weight:600;letter-spacing:1px}
.hero-right{width:50%;background:linear-gradient(160deg,#2b7fd0,#1a5fa6);color:var(--white);padding:36px 60px 0 50px}
.hero-right h2{font-size:15px;font-weight:600;margin-bottom:24px}
.steps{display:grid;grid-template-columns:repeat(4,1fr);gap:18px 20px;width:440px}
.step{display:flex;flex-direction:column;align-items:center;font-size:9px;text-align:center;gap:6px}
.step svg{width:54px;height:54px}
.hero-cta{position:absolute;left:50%;bottom:24px;transform:translateX(-50%);background:var(--hero-dark);color:var(--white);font-size:11px;font-weight:700;padding:9px 20px;border:1px solid rgba(255,255,255,.4)}
.hero-band{height:10px;background:var(--blue-dark)}

/* section headings */
.section-title{text-align:center;font-size:28px;font-weight:700;color:var(--ink);text-transform:uppercase}
.section-title span{color:var(--blue)}
.title-rule{width:520px;height:1px;background:var(--line);margin:12px auto 0}

/* services */
.services{padding-top:34px}
.service-list{display:flex;justify-content:center;gap:90px;margin-top:36px}
.service{width:220px;text-align:center}
.service svg{width:78px;height:78px;margin-bottom:14px}
.service h3{font-size:13px;font-weight:700;margin-bottom:10px}
.service p{font-size:11px;line-height:1.55;color:var(--muted)}

/* video */
.video{margin:46px auto 0;width:600px;height:360px;position:relative}
.video-frame{width:600px;height:340px;background:#1c1c1c;padding:10px;border-radius:4px}
.video-still{width:100%;height:100%;background:linear-gradient(135deg,#9a7a57,#c9a57a 55%,#7d6247)}
.video-play{position:absolute;left:50%;top:170px;transform:translate(-50%,-50%);width:70px;height:70px}
.video-base{width:640px;height:14px;margin:-2px 0 0 -20px;background:linear-gradient(#d6d6d6,#a9a9a9);border-radius:0 0 40px 40px}

/* plans */
.get-started{margin-top:42px}
.plans{background:var(--orange);margin-top:26px;height:470px;padding:30px 0}
.plan-grid{display:flex;justify-content:center;gap:30px}
.plan{width:440px;background:var(--white);border:1px solid #e2e2e2}
.plan-photo{height:200px;margin:14px;background:radial-gradient(circle,#9aa0a6,#e9e9e9 70%)}
.plan-photo.dark{background:radial-gradient(circle,#4a4f55,#eeeeee 70%)}
.plan-price{background:var(--panel-grey);color:var(--white);text-align:center;padding:8px;font-size:13px}
.plan-price strong{font-size:19px}
.plan-row{background:var(--orange-deep);color:var(--white);text-align:center;font-size:12px;padding:7px;border-top:2px solid var(--white)}
.plan-row.spec{background:var(--orange-deep);line-height:1.4}

/* before / after */
.transform{margin:34px auto 0;width:1000px;background:var(--light);border:1px solid var(--line);height:210px;display:flex;padding:18px 22px;gap:24px}
.transform-text{flex:1}
.transform-text h3{font-size:17px;font-weight:600;color:var(--blue);margin-bottom:10px}
.transform-text li{font-size:11px;color:var(--muted);list-style:none;margin-bottom:5px}
.transform-text li::before{content:"✔ ";color:var(--orange)}
.transform-text p{font-size:11px;color:var(--muted);line-height:1.5;margin-top:10px}
.compare{display:flex;gap:12px}
.compare figure{width:190px}
.compare figcaption{background:var(--orange-deep);color:var(--white);font-size:11px;font-weight:700;text-align:center;padding:3px}
.compare .shot{height:140px;background:linear-gradient(135deg,#8e7d66,#c6b79c)}
.compare .shot.after{background:linear-gradient(135deg,#cfd6dd,#f3f3f0)}

/* quote */
.quote{margin-top:40px}
.quote-form{width:560px;margin:30px auto 0;display:grid;grid-template-columns:1fr 1fr;gap:12px 20px}
.field{height:34px;border:1px solid var(--line);background:var(--white);font-size:11px;color:#999;padding:9px 10px}
.quote-btn{display:block;width:170px;margin:24px auto 0;background:var(--blue);color:var(--white);text-align:center;font-size:12px;font-weight:700;padding:10px}

/* footer */
.site-footer{position:absolute;left:0;right:0;bottom:38px;height:230px;background:var(--footer);color:#cfd2d5}
.site-footer .wrap{display:flex;gap:70px;padding-top:26px}
.site-footer h4{color:var(--white);font-size:13px;font-weight:700;margin-bottom:14px}
.msg-form{width:260px}
.msg-row{display:flex;align-items:center;gap:10px;margin-bottom:8px;font-size:10px}
.msg-row label{width:60px}
.msg-row .box{flex:1;height:20px;background:var(--white)}
.msg-row .box.tall{height:44px}
.msg-send{margin-left:70px;width:60px;background:var(--blue);color:var(--white);font-size:10px;text-align:center;padding:4px}
.links li{list-style:none;font-size:11px;margin-bottom:7px}
.links li::before{content:"✔ ";color:var(--blue)}
.help li{list-style:none;font-size:11px;margin-bottom:7px}
.help li span{color:var(--blue);margin-right:6px}
.bottom-bar{position:absolute;left:0;right:0;bottom:0;height:38px;background:var(--footer-bottom);color:#8a8e92;font-size:10px}
.bottom-bar .wrap{display:flex;justify-content:space-between;align-items:center;height:38px}
.socials{display:flex;gap:6px}
.socials i{width:20px;height:20px;background:#3d4247;display:block}
</style>
</head>
<body>

<header class="site-header">
  <div class="wrap">
    <div class="brand"><span class="brand-mark"></span>Tralha Cesto</div>
    <nav class="main-nav">
      <a class="active">HOME</a><a>PRICING</a><a>SECURITY</a><a>ABOUT US</a><a>PRESS</a><a>LOGIN</a><a>FAQ</a><a>CONTACT US</a>
      <a class="search"><svg width="14" height="14" viewBox="0 0 14 14"><circle cx="6" cy="6" r="4.5" fill="none" stroke="#777" stroke-width="1.6"/><line x1="9.3" y1="9.3" x2="13" y2="13" stroke="#777" stroke-width="1.6"/></svg></a>
    </nav>
  </div>
</header>

<section class="hero">
  <div class="hero-left">
    <h1>TRALHA CESTO</h1>
    <div class="rule"></div>
    <p>STORAGE MADE SIMPLE!</p>
  </div>
  <div class="hero-right">
    <h2>We manage pick up, storage and retrieval for you.</h2>
    <div class="steps">
      <div class="step"><svg viewBox="0 0 54 54"><circle cx="27" cy="27" r="25" fill="#fff"/><rect x="16" y="20" width="22" height="16" fill="none" stroke="#1f6fc0" stroke-width="2"/></svg>Peça caixas</div>
      <div class="step"><svg viewBox="0 0 54 54"><circle cx="27" cy="27" r="25" fill="#fff"/><path d="M14 32h18v-10h6l4 6v4z" fill="none" stroke="#1f6fc0" stroke-width="2"/></svg>Entregamos</div>
      <div class="step"><svg viewBox="0 0 54 54"><circle cx="27" cy="27" r="25" fill="#fff"/><path d="M16 24l11-6 11 6v12H16z" fill="none" stroke="#1f6fc0" stroke-width="2"/></svg>Você enche</div>
      <div class="step"><svg viewBox="0 0 54 54"><circle cx="27" cy="27" r="25" fill="#fff"/><path d="M20 16h14v22H20z M24 34h6" fill="none" stroke="#1f6fc0" stroke-width="2"/></svg>Nos ligue</div>
      <div class="step"><svg viewBox="0 0 54 54"><circle cx="27" cy="27" r="25" fill="#fff"/><path d="M14 32h18v-10h6l4 6v4z" fill="none" stroke="#1f6fc0" stroke-width="2"/></svg>Coletamos</div>
      <div class="step"><svg viewBox="0 0 54 54"><circle cx="27" cy="27" r="25" fill="#fff"/><path d="M15 22h24v16H15z M15 22l12-6 12 6" fill="none" stroke="#1f6fc0" stroke-width="2"/></svg>Guardamos</div>
      <div class="step"><svg viewBox="0 0 54 54"><circle cx="27" cy="27" r="25" fill="#fff"/><rect x="15" y="18" width="24" height="16" fill="none" stroke="#1f6fc0" stroke-width="2"/><path d="M22 38h10" stroke="#1f6fc0" stroke-width="2"/></svg>Peça online</div>
      <div class="step"><svg viewBox="0 0 54 54"><circle cx="27" cy="27" r="25" fill="#fff"/><path d="M17 27l7 7 13-14" fill="none" stroke="#1f6fc0" stroke-width="3"/></svg>Devolvemos</div>
    </div>
  </div>
  <a class="hero-cta">HOW IT WORKS</a>
</section>
<div class="hero-band"></div>

<section class="services">
  <h2 class="section-title">Our outstanding <span>Services</span></h2>
  <div class="title-rule"></div>
  <div class="service-list">
    <div class="service">
      <svg viewBox="0 0 78 78"><circle cx="39" cy="39" r="37" fill="#e9e9e9"/><rect x="26" y="36" width="26" height="20" rx="2" fill="#555"/><path d="M31 36v-6a8 8 0 0 1 16 0v6" fill="none" stroke="#555" stroke-width="4"/></svg>
      <h3>SEGURANÇA</h3>
      <p>Todos os seus itens armazenados em um ambiente seguro, monitorado 24 horas por dia.</p>
    </div>
    <div class="service">
      <svg viewBox="0 0 78 78"><circle cx="39" cy="39" r="37" fill="#e9e9e9"/><path d="M24 40l10 10 20-22" fill="none" stroke="#555" stroke-width="6"/></svg>
      <h3>PRATICIDADE</h3>
      <p>Escolha o atendimento de sua comodidade na sua casa, em dias úteis ou sábados, na Grande São Paulo.</p>
    </div>
    <div class="service">
      <svg viewBox="0 0 78 78"><circle cx="39" cy="39" r="37" fill="#e9e9e9"/><circle cx="39" cy="39" r="17" fill="none" stroke="#555" stroke-width="4"/><text x="39" y="46" text-anchor="middle" font-family="Open Sans,Arial,sans-serif" font-weight="700" font-size="20" fill="#555">$</text></svg>
      <h3>ECONOMIA</h3>
      <p>Aproveite melhor o espaço que você já tem dentro de casa.</p>
    </div>
  </div>
</section>

<div class="video">
  <div class="video-frame"><div class="video-still" role="img" aria-label="Explainer video still: a person packing cardboard boxes"></div></div>
  <svg class="video-play" viewBox="0 0 70 70"><circle cx="35" cy="35" r="33" fill="rgba(0,0,0,.45)" stroke="#fff" stroke-width="3"/><path d="M28 22l20 13-20 13z" fill="#fff"/></svg>
  <div class="video-base"></div>
</div>

<section class="get-started">
  <h2 class="section-title">Get <span>Started</span></h2>
  <div class="title-rule"></div>
  <div class="plans">
    <div class="plan-grid">
      <div class="plan">
        <div class="plan-photo" role="img" aria-label="Large grey storage container"></div>
        <div class="plan-price">a partir de <strong>$69,00</strong> / mes</div>
        <div class="plan-row spec">Dimensoes Largura × Comprimento<br>× Altura / Volume total: 800 Litros</div>
        <div class="plan-row">Valor armazenagem</div>
        <div class="plan-row">Valor entrega nos Pontos de Coleta</div>
        <div class="plan-row">Valor em domicilio</div>
      </div>
      <div class="plan">
        <div class="plan-photo dark" role="img" aria-label="Black plastic storage crate"></div>
        <div class="plan-price">a partir de <strong>$14,90</strong> / mes</div>
        <div class="plan-row spec">Dimensoes Largura × Comprimento<br>× Altura / Volume total: 80 Litros</div>
        <div class="plan-row">Valor armazenagem</div>
        <div class="plan-row">Valor entrega nos Pontos de Coleta</div>
        <div class="plan-row">Valor em domicilio</div>
      </div>
    </div>
  </div>
</section>

<section class="transform">
  <div class="transform-text">
    <h3>Transforme o seu quarto da tralha em um quarto de verdade</h3>
    <ul>
      <li>A família vai aumentar?</li>
      <li>Quer receber bem aquele parente?</li>
      <li>Está se mudando para um lugar menor?</li>
    </ul>
    <p>Reconquiste o espaço de sua casa guardando tudo aquilo que você usa pouco em uma das nossas caixas.</p>
    <p>Mais que o precioso espaço de sua casa conquistado, Tralha Cesto guarda tudo para você.</p>
  </div>
  <div class="compare">
    <figure><figcaption>ANTES</figcaption><div class="shot" role="img" aria-label="Cluttered room full of boxes before"></div></figure>
    <figure><figcaption>DEPOIS</figcaption><div class="shot after" role="img" aria-label="Tidy bright room after"></div></figure>
  </div>
</section>

<section class="quote">
  <h2 class="section-title">Request a <span>Quote</span></h2>
  <div class="title-rule"></div>
  <div class="quote-form">
    <div class="field">Name</div><div class="field">Zip Code</div>
    <div class="field">Email</div><div class="field">Phone</div>
  </div>
  <a class="quote-btn">GET FREE QUOTE</a>
</section>

<footer class="site-footer">
  <div class="wrap">
    <div class="msg-form">
      <h4>LEAVE A MESSAGE</h4>
      <div class="msg-row"><label>Your Name</label><span class="box"></span></div>
      <div class="msg-row"><label>E-mail</label><span class="box"></span></div>
      <div class="msg-row"><label>Subject</label><span class="box"></span></div>
      <div class="msg-row"><label>Message</label><span class="box tall"></span></div>
      <div class="msg-send">SEND</div>
    </div>
    <div>
      <h4>SPECIAL LINKS</h4>
      <ul class="links">
        <li>Frequently Asked Questions</li><li>In the Press</li><li>Privacy Policy</li><li>Shipment &amp; Storage</li><li>Terms of Service</li><li>Blog</li>
      </ul>
    </div>
    <div>
      <h4>LET US HELP</h4>
      <ul class="help">
        <li><span>✆</span>+55 11 5555-0100</li>
        <li><span>✉</span>contato@tralhacesto.example</li>
        <li><span>◷</span>Customer Service Hours: 9AM - 9PM, Mon - Sat</li>
        <li><span>◷</span>Delivery Hours: 8AM - 8PM, Mon - Sun</li>
      </ul>
    </div>
  </div>
</footer>
<div class="bottom-bar">
  <div class="wrap">
    <span>Copyright © 2014 Tralha Cesto. All rights reserved.</span>
    <div class="socials"><i></i><i></i><i></i><i></i></div>
  </div>
</div>

</body>
</html>
```